Business Card Design

I need a business card for a new company based in Australia called "MedLinkora".

Its a cloud program for GPs that allows them to search for the specialist they require using a simple user friendly tool.

I would like the colours to match those in the program (the colours in the logo attached).

The final design should reflect the programs clarity, ease of use and professionalism.

Target Market(s)

GPs and other Health Professionals

Industry/Entity Type

Business

Contact Information for Business Card

MedLinkora; The Whole Consultant Index; Marla Voss CEO; 0438215967; marla@medlinkora.example; www.medlinkora.example

Requirements
Must have
• Must have the logo attached; the web address and my name and phone number
Nice to have
• the slogan "The Whole Consultant Index"

```html
<!DOCTYPE html>
<html lang="en">
<head>
<meta charset="utf-8">
<title>MedLinkora Business Card</title>
<link rel="stylesheet" href="https://fonts.googleapis.com/css2?family=Open+Sans:wght@400;600;700&display=swap">
<style>
  :root {
    --brand-cyan: #19b1e6;
    --ink: #2b2b2b;
    --muted: #8a8a8a;
    --paper: #ffffff;
    --card-dark: #050505;
    --backdrop: #e9e9e9;
    --rule: #d4d4d4;
  }
  * { margin: 0; padding: 0; box-sizing: border-box; }
  html, body {
    width: 1200px; height: 1200px; overflow: hidden;
    background: var(--backdrop);
    font-family: "Open Sans", Arial, sans-serif;
  }
  .stage {
    width: 1200px; height: 1200px;
    display: flex; flex-direction: column; align-items: center; justify-content: center;
    gap: 60px;
  }
  .card {
    width: 780px; height: 450px;
    border-radius: 40px;
    display: flex; flex-direction: column; align-items: center;
    box-shadow: 0 2px 10px rgba(0,0,0,0.12);
  }
  .card--front { background: var(--paper); padding-top: 70px; }
  .card--back { background: var(--card-dark); padding-top: 110px; }

  .brand-name {
    font-weight: 600; font-size: 84px; line-height: 1;
    color: var(--brand-cyan); letter-spacing: -1px;
  }
  .tagline {
    font-size: 25px; color: var(--muted); margin-top: 8px; letter-spacing: 0.5px;
  }
  .card--back .brand-name { font-size: 96px; }
  .card--back .tagline { color: #b9b9b9; font-size: 28px; }

  .holder { margin-top: 62px; font-size: 30px; }
  .holder__name { font-weight: 700; color: var(--brand-cyan); }
  .holder__role { color: var(--muted); font-size: 26px; }

  .divider {
    width: 640px; height: 3px; margin-top: 22px;
    background: linear-gradient(90deg, transparent, var(--rule) 15%, var(--rule) 85%, transparent);
  }
  .contact { display: flex; align-items: center; gap: 10px; color: var(--ink); }
  .contact svg { flex: none; }
  .contact--phone { margin-top: 18px; font-size: 30px; }
  .contact-row { display: flex; gap: 26px; margin-top: 14px; font-size: 24px; }

  .web-address {
    margin-top: 56px; color: #f2f2f2; font-size: 34px; letter-spacing: 4px;
  }
</style>
</head>
<body>
<main class="stage">
  <section class="card card--front" aria-label="Business card front">
    <div class="brand-name">MedLinkora</div>
    <div class="tagline">The Whole Consultant Index</div>
    <div class="holder"><span class="holder__name">Marla Voss,</span> <span class="holder__role">CEO</span></div>
    <div class="divider"></div>
    <div class="contact contact--phone">
      <svg width="30" height="30" viewBox="0 0 30 30" aria-hidden="true">
        <circle cx="15" cy="15" r="13" fill="none" stroke="var(--brand-cyan)" stroke-width="2"/>
        <path d="M11 8c-1.5 1-2 3 -1 6s3 6 6 7.5c1.5.7 3 .3 4-1l-2.5-2.5-2 1c-1.5-1-3-3-3.5-4.5l1.5-1.5z" fill="var(--brand-cyan)"/>
      </svg>
      <span>0438215967</span>
    </div>
    <div class="contact-row">
      <div class="contact">
        <svg width="26" height="20" viewBox="0 0 26 20" aria-hidden="true">
          <rect x="1" y="2" width="24" height="16" rx="2" fill="var(--brand-cyan)"/>
          <path d="M2 3l11 9 11-9" fill="none" stroke="#fff" stroke-width="2"/>
        </svg>
        <span>marla@medlinkora.example</span>
      </div>
      <div class="contact">
        <svg width="24" height="24" viewBox="0 0 24 24" aria-hidden="true">
          <g fill="none" stroke="var(--brand-cyan)" stroke-width="1.8">
            <circle cx="12" cy="12" r="10"/>
            <ellipse cx="12" cy="12" rx="4.5" ry="10"/>
            <path d="M2 12h20M4 6.5h16M4 17.5h16"/>
          </g>
        </svg>
        <span>www.medlinkora.example</span>
      </div>
    </div>
  </section>

  <section class="card card--back" aria-label="Business card back">
    <div class="brand-name">MedLinkora</div>
    <div class="tagline">The Whole Consultant Index</div>
    <div class="web-address">www.medlinkora.example</div>
  </section>
</main>
</body>
</html>
```